Business card for marketing analytics company

Need a business card for new company. I have a logo already that I want to be built into the card and should use those colours

Company is called steered by tallies
Design must bring steered by tallies to life not be a card that could be for anyone with a logo put on it.

Like the front to be fairly clean and uncluttered bringing the logo out with a suitable design on the back of the card.

The logo represents a compass and business growth so those themes along with numbers, analytics , data are appropriate.
I'm often working with creative industries so also needs to reflect the creative side of analytics rather than be very corporate looking.

Target Market(s)

Ad agency, media agency, consumer goods clients

Industry/Entity Type

Market Research

Contact Information for Business Card

Needs to include name, title, email and phone number

Colors
f78f20
f68d4d
ec1f27

Requirements
Must have
• Must bring steered by tallies to life not be a card that could be for anyone with a logo put on it.
• Logo, Correct colours
• Like a design on the back that relates to company name
• Designs for both sides
Should not have
• Please do not just submit logo and a coloured card.
• It needs to have a design element to it
• No black background
• No clear cards - needs front & back

```html
<!DOCTYPE html>
<html lang="en">
<head>
<meta charset="utf-8">
<title>Kestrel Ledger – Business Card</title>
<link href="https://fonts.googleapis.com/css2?family=Lato:wght@400;700;900&display=swap" rel="stylesheet">
<style>
  :root {
    --red: #ec1f27;
    --orange-burnt: #e8611e;
    --ink: #3a3d42;
    --slate: #4c5258;
    --paper: #ffffff;
    --paper-shade: #eeeeee;
    --chart-faint: #f6d9d9;
    --chart-node: #e6e6e6;
    --stage: #e4e4e4;
  }
  * { box-sizing: border-box; margin: 0; padding: 0; }
  html, body { width: 1200px; height: 997px; overflow: hidden; }
  body {
    background: var(--stage);
    font-family: "Lato", sans-serif;
    position: relative;
  }
  .card {
    position: absolute;
    left: 250px;
    width: 700px;
    height: 400px;
    overflow: hidden;
    box-shadow: 0 6px 18px rgba(0,0,0,.18);
  }
  .card--back { top: 48px; }
  .card--front { top: 518px; background: linear-gradient(180deg, var(--paper), var(--paper-shade)); }
  .card svg.art { position: absolute; inset: 0; }

  .wordmark {
    position: absolute;
    font-weight: 700;
    line-height: 1.05;
    display: flex;
    align-items: center;
    gap: 12px;
  }
  .wordmark__dot { border-radius: 50%; flex: none; }
  .card--back .wordmark { left: 46px; top: 150px; color: var(--paper); font-size: 30px; }
  .card--back .wordmark__dot { width: 44px; height: 44px; border: 3px solid var(--paper); }
  .card--front .wordmark { left: 232px; top: 36px; color: var(--ink); font-size: 30px; }
  .card--front .wordmark__dot { width: 50px; height: 50px; background: var(--red); }

  .band { position: absolute; left: 0; width: 100%; background: var(--orange-burnt); }
  .band--name { top: 120px; height: 40px; }
  .band--rule { top: 262px; height: 14px; }

  .person { position: absolute; left: 0; width: 100%; top: 124px; text-align: center; }
  .person__name { color: var(--paper); font-weight: 900; font-size: 26px; letter-spacing: .5px; text-transform: uppercase; line-height: 32px; }
  .person__title { color: var(--ink); font-size: 15px; margin-top: 10px; }

  .office { position: absolute; right: 34px; top: 186px; text-align: right; color: var(--ink); font-size: 17px; line-height: 1.3; }
  .office__name { color: var(--orange-burnt); font-weight: 700; font-size: 18px; text-transform: uppercase; }

  .contacts { position: absolute; left: 36px; top: 296px; list-style: none; color: var(--ink); font-size: 18px; }
  .contacts li { display: flex; align-items: center; gap: 12px; height: 28px; }
  .contacts svg { flex: none; }

  .foot-strip { position: absolute; left: 0; bottom: 0; width: 100%; height: 18px; background: var(--slate); }
  .foot-tab { position: absolute; right: 0; bottom: 18px; width: 230px; height: 36px; background: var(--orange-burnt); border-top-left-radius: 36px; }
</style>
</head>
<body>

<section class="card card--back" aria-label="Card back">
  <svg class="art" width="700" height="400" viewBox="0 0 700 400">
    <rect width="700" height="400" fill="var(--orange-burnt)"/>
    <polygon points="0,0 640,0 600,110 500,215 390,200 300,215 190,350 60,400 0,400" fill="var(--red)"/>
    <g role="img" aria-label="Growth line chart filled with scattered numbers">
      <polyline points="30,400 60,390 190,350 300,215 390,200 500,215 600,110 640,0"
        fill="none" stroke="var(--chart-node)" stroke-width="22" stroke-linejoin="round"/>
      <circle cx="60" cy="388" r="36" fill="var(--chart-node)"/>
      <circle cx="190" cy="350" r="30" fill="var(--chart-node)"/>
      <circle cx="300" cy="215" r="36" fill="var(--chart-node)"/>
      <circle cx="500" cy="215" r="38" fill="var(--chart-node)"/>
      <circle cx="600" cy="110" r="26" fill="var(--chart-node)"/>
      <circle cx="640" cy="10" r="34" fill="var(--chart-node)"/>
    </g>
  </svg>
  <div class="wordmark"><span class="wordmark__dot"></span><span>Kestrel<br>Ledger</span></div>
</section>

<section class="card card--front" aria-label="Card front">
  <svg class="art" width="700" height="400" viewBox="0 0 700 400" role="img" aria-label="Faint growth line chart made of numbers">
    <polyline points="20,360 120,330 210,230 300,250 420,240 470,290 540,140 600,90 700,70"
      fill="none" stroke="var(--chart-faint)" stroke-width="26" stroke-linejoin="round"/>
    <circle cx="20" cy="360" r="34" fill="var(--chart-faint)"/>
    <circle cx="470" cy="290" r="32" fill="var(--chart-faint)"/>
    <circle cx="540" cy="140" r="36" fill="var(--chart-faint)"/>
    <circle cx="300" cy="250" r="30" fill="var(--chart-faint)"/>
  </svg>

  <div class="wordmark"><span class="wordmark__dot"></span><span>Kestrel<br>Ledger</span></div>

  <div class="band band--name"></div>
  <div class="band band--rule"></div>

  <div class="person">
    <div class="person__name">Marcus Delaney</div>
    <div class="person__title">Director</div>
  </div>

  <div class="office">
    <div class="office__name">Kestrel Ledger</div>
    <div>27, Mill Lane, near the</div>
    <div>Old Bridge, Kendal.</div>
  </div>

  <ul class="contacts">
    <li>
      <svg width="18" height="18" viewBox="0 0 18 18" aria-hidden="true"><circle cx="9" cy="9" r="9" fill="var(--orange-burnt)"/><path d="M6 4.5h2l.6 2.4-1.2.8a5 5 0 0 0 2.9 2.9l.8-1.2 2.4.6v2c-4.5.3-7.8-3-7.5-7.5z" fill="var(--paper)"/></svg>
      <span>08451237790</span>
    </li>
    <li>
      <svg width="18" height="18" viewBox="0 0 18 18" aria-hidden="true"><circle cx="9" cy="9" r="9" fill="var(--orange-burnt)"/><rect x="4.5" y="6" width="9" height="6.5" fill="var(--paper)"/><path d="M4.5 6l4.5 3.6L13.5 6" fill="none" stroke="var(--orange-burnt)" stroke-width="1"/></svg>
      <span>mdelaney@tallyfield.com.au</span>
    </li>
    <li>
      <svg width="18" height="18" viewBox="0 0 18 18" aria-hidden="true"><circle cx="9" cy="9" r="9" fill="var(--orange-burnt)"/><circle cx="9" cy="9" r="4.5" fill="none" stroke="var(--paper)" stroke-width="1.2"/><path d="M4.5 9h9M9 4.5c-2 2.5-2 6.5 0 9M9 4.5c2 2.5 2 6.5 0 9" fill="none" stroke="var(--paper)" stroke-width="1"/></svg>
      <span>www.tallyfield.com.au</span>
    </li>
  </ul>

  <div class="foot-tab"></div>
  <div class="foot-strip"></div>
</section>

</body>
</html>
```